Window company.

Hello,

We are a small family business located in Madrid, Spain that works nationwide to fix, change or mount the windows of your home / premises.

The group of possible clients to whom the flyer is focused ranges from 30 to 65 years, families in general who want comfort at home and extra savings every year in heating.

It must include not only graphics and a striking aesthetic in accordance with the concepts of wanting to reach / transmit the final product to the customer to sell the product.

Details to also include:

-Brief history of the company and its foundation in 2006. It will be subsequently translated into Spanish so put in words what you consider necessary so that the client stays with the concept that we are professionals.

--Specialized in exterior aluminum and PVC carpentry.

-We move to your home for a first visit and we provide the budget totally free without any commitment.

- Also payment facilities; up to 3 times, without interest.

-Contact details of the company. (WhatsApp, email, phone and location)
Open: Mon - Friday 11,00am - 9pm
Saturday: 12,00am - 7pm
Sunday: Closed

Also as a suggestion, to decide on your own, graphics of types of window openings, if you consider that anything that is striking for the client so it wonr be yet another advertising flyer.

We are open to all kinds of ideas, all of them involving marketing branding.

We are open to any type of idea and we want to stand out, the construction world is tough and we have an idea to grow, taking into account that it must not only be beautiful but commercial to attract potential customers with all kinds of purchasing power.

Thank you.

```html
<!DOCTYPE html>
<html lang="en">
<head>
<meta charset="utf-8">
<title>Ventara – Window Flyer</title>
<link rel="stylesheet" href="https://fonts.googleapis.com/css2?family=Open+Sans:wght@400;600;700&family=Roboto:wght@300;700&family=Raleway:wght@400&display=swap">
<style>
  :root{
    --brand-red:#d11f42;
    --deep-red:#9b0f2a;
    --ink:#151515;
    --paper:#ffffff;
    --mist:#e8e9eb;
    --stage:#cccccc;
    --name-grey:#b3ab9f;
  }
  html,body{margin:0;padding:0;width:1200px;height:1200px;overflow:hidden;background:var(--stage);}
  .flyer{position:absolute;left:176px;top:0;width:847px;height:1200px;background:var(--paper);overflow:hidden;font-family:"Open Sans",sans-serif;}
  .abs{position:absolute;margin:0;}

  .brand{left:50px;top:98px;display:flex;align-items:center;gap:10px;font-family:"Open Sans",sans-serif;font-weight:700;font-size:30px;letter-spacing:1px;color:var(--name-grey);}
  .brand-square{width:16px;height:16px;background:var(--brand-red);}

  .quote{right:33px;top:54px;text-align:right;color:var(--brand-red);}
  .quote-label{font-family:"Open Sans",sans-serif;font-size:26px;line-height:30px;}
  .quote-phone{font-family:"Roboto",sans-serif;font-weight:700;font-size:32px;line-height:34px;}

  .hero{left:0;top:146px;width:847px;height:399px;background:linear-gradient(100deg,#55605e 0%,#8fa39c 25%,#c9cccd 45%,#dcdcde 60%,#5f7358 80%,#9aa79a 100%);}
  .top-band{left:311px;top:146px;width:536px;height:14px;background:var(--brand-red);}

  .offer{left:0;top:545px;width:847px;height:264px;background:var(--brand-red);color:var(--paper);}
  .offer-title{left:81px;top:22px;font-family:"Roboto",sans-serif;font-weight:300;font-size:30px;line-height:34px;}
  .offer-title strong{font-weight:700;}
  .offer-rule{left:81px;top:67px;width:652px;height:1px;background:var(--paper);}
  .offer-list{left:81px;top:83px;list-style:none;padding:0;font-size:23px;line-height:27px;}
  .offer-list li{position:relative;padding-left:14px;margin-bottom:16px;}
  .offer-list li::before{content:"•";position:absolute;left:0;top:-1px;font-size:15px;}

  .work{top:0;width:100%;height:100%;}
  .gallery{left:0;top:809px;width:847px;height:260px;background:var(--mist);}
  .shot{top:823px;width:259px;height:202px;}
  .shot-a{left:31px;background:linear-gradient(120deg,#d8dde2,#3d5fa3 45%,#eef0f2);}
  .shot-b{left:296px;background:linear-gradient(120deg,#b08a63,#6d5a4a 45%,#e0a53a);}
  .shot-c{left:561px;background:linear-gradient(120deg,#3b3b3b,#c99a6c 50%,#e4e4e4);}

  .footer-wave{left:0;top:1000px;width:847px;height:200px;}

  .hours{left:31px;top:1107px;font-weight:700;font-size:17.5px;line-height:23px;color:var(--paper);}
  .hours .dark{color:var(--ink);}
  .hours .indent{padding-left:60px;display:block;}

  .pin{left:443px;top:1130px;width:32px;height:46px;}
  .address{left:520px;top:1131px;width:236px;text-align:center;font-family:"Raleway",sans-serif;font-size:16.5px;line-height:23px;color:var(--paper);white-space:nowrap;}
</style>
</head>
<body>
<main class="flyer">
  <header>
    <div class="abs brand"><span class="brand-square"></span>VENTARA</div>
    <div class="abs quote">
      <div class="quote-label">Call us for free quote</div>
      <div class="quote-phone">+34 611 42 57 19</div>
    </div>
  </header>

  <div class="abs hero" role="img" aria-label="Modern house facade with large black-framed glass windows and sliding doors"></div>
  <div class="abs top-band"></div>

  <section class="abs offer">
    <h2 class="abs offer-title">WHAT <strong>WE OFFER?</strong></h2>
    <div class="abs offer-rule"></div>
    <ul class="abs offer-list">
      <li>Specialized in exterior &nbsp;aluminum and PVC carpentry.</li>
      <li>We move to your home &nbsp;for a first visit and we provide<br>the budget totally free without any commitment.</li>
      <li>Also payment facilities; up to 3 times, without interest.</li>
    </ul>
  </section>

  <div class="abs gallery"></div>
  <div class="abs shot shot-a" role="img" aria-label="Worker in blue overalls fitting a white PVC window"></div>
  <div class="abs shot shot-b" role="img" aria-label="Installer in hard hat placing glass with suction cups"></div>
  <div class="abs shot shot-c" role="img" aria-label="Hands adjusting an aluminium window frame with a screwdriver"></div>

  <svg class="abs footer-wave" viewBox="0 0 847 200" preserveAspectRatio="none">
    <defs>
      <linearGradient id="footerRed" x1="0" y1="0" x2="1" y2="0">
        <stop offset="0" stop-color="var(--deep-red)"/>
        <stop offset="1" stop-color="var(--brand-red)"/>
      </linearGradient>
    </defs>
    <path d="M0,13 C200,90 500,108 847,110 L847,200 L0,200 Z" fill="url(#footerRed)"/>
    <path d="M0,2 C200,79 500,97 847,99 L847,110 C500,108 200,90 0,13 Z" fill="#ffffff"/>
  </svg>

  <div class="abs hours">
    <span class="dark">Open:</span> Mon - Friday 11,00am - 9pm
    <span class="indent">Saturday: 12,00am - 7pm</span>
    <span class="indent dark">Sunday: Closed</span>
  </div>

  <svg class="abs pin" viewBox="0 0 32 46" aria-hidden="true">
    <path d="M16 0C7.2 0 0 7 0 15.6 0 27 16 46 16 46S32 27 32 15.6C32 7 24.8 0 16 0Z" fill="var(--ink)"/>
    <circle cx="16" cy="15" r="6" fill="var(--brand-red)"/>
  </svg>
  <div class="abs address">Pol. Ind. Las Acacias, Nave 14<br>Getafe, Spain 28906</div>
</main>
</body>
</html>
```